Small butcher shop from Austria needs great powerpoint presentation

We are looking for a powerpoint template for our new CI - it should be modern and clear.

Logo (2 Versions), Slogan, Business Card and Car-Wrap-Design already exist. (See documents below.)

We won't use much text. About 50% of the presentation should be pictures, included in different ways.

We are a family business in Upper Austria, only process animals from farms in the immediate vicinity, produce the products by hand, value animal welfare and short transport routes and avoid packaging as much as possible.

The design should be modern and clear.

Sans Serif

• Use the red color sparingly. Only use sans serif fonts (Myriad Pro - if possible). The logo needs to be on first and last page only.

```html
<!DOCTYPE html>
<html lang="en">
<head>
<meta charset="utf-8">
<title>Halder Presentation Template</title>
<link href="https://fonts.googleapis.com/css2?family=Poppins:ital,wght@0,400;0,500;0,600;0,700;1,500&display=swap" rel="stylesheet">
<style>
  :root {
    --red: #7b0e1f;
    --red-mid: #8a1628;
    --red-soft: #9a2435;
    --dark: #1c2321;
    --ink: #1f1f1f;
    --body: #3a3a3a;
    --rule: #d9d9d9;
    --page: #eff0f2;
    --white: #ffffff;
  }
  * { margin: 0; padding: 0; box-sizing: border-box; }
  html, body { width: 1200px; height: 3987px; overflow: hidden; }
  body { background: var(--page); font-family: "Poppins", sans-serif; color: var(--ink); position: relative; }

  .slide { position: absolute; left: 68px; width: 1065px; height: 598px; overflow: hidden; background: var(--white); box-shadow: 0 1px 4px rgba(0,0,0,.08); }
  .photo { position: absolute; }

  .page-no { position: absolute; right: -52px; bottom: -54px; width: 114px; height: 114px; border-radius: 50%; background: var(--red); }
  .page-no span { position: absolute; left: 22px; top: 14px; color: var(--white); font-weight: 600; font-size: 23px; }

  /* Cover */
  .cover { top: 59px; background: linear-gradient(180deg, #7d1020 0%, #86172a 100%); text-align: center; color: var(--white); }
  .cover .scene { position: absolute; inset: 0; background: radial-gradient(ellipse at 60% 45%, rgba(160,50,65,.35), transparent 60%); }
  .brand { position: absolute; left: 0; right: 0; font-weight: 600; letter-spacing: 10px; }
  .cover .brand { top: 170px; font-size: 84px; line-height: 1; }
  .cover-title { position: absolute; left: 0; right: 0; top: 352px; font-size: 62px; font-weight: 700; line-height: 1.2; }
  .cover-sub { position: absolute; left: 0; right: 0; top: 428px; font-size: 34px; font-weight: 400; }
  .cover-url { position: absolute; left: 0; right: 0; top: 547px; font-size: 18px; font-weight: 500; letter-spacing: 7px; }

  /* Text slides */
  .text-slide .side { position: absolute; left: 0; top: 0; width: 277px; height: 100%; background: var(--dark); }
  .text-slide .photo { left: 88px; top: 50px; width: 443px; height: 498px; }
  .text-block { position: absolute; left: 576px; top: 112px; width: 460px; }
  .text-block h2 { font-size: 25px; font-weight: 700; line-height: 1.38; margin-bottom: 18px; }
  .text-block p { font-size: 14px; line-height: 30.6px; color: var(--body); }

  /* Points slide */
  .points-slide { top: 1350px; }
  .points-slide .side { position: absolute; left: 0; top: 0; width: 443px; height: 100%; background: var(--red); }
  .points { position: absolute; left: 602px; top: 126px; width: 443px; list-style: none; }
  .points li { display: flex; align-items: center; height: 127px; border-top: 1px solid var(--rule); }
  .points li:first-child { border-top: 0; height: 117px; margin-top: -18px; }
  .points .num { width: 80px; height: 80px; border-radius: 50%; background: var(--red); color: var(--white); font-size: 27px; font-weight: 500; display: flex; align-items: center; justify-content: center; flex: none; margin-right: 10px; }
  .points h3 { font-size: 21px; font-weight: 600; line-height: 1.2; }
  .points p { font-size: 14px; line-height: 23px; color: var(--body); }

  /* Quote slide */
  .quote-slide { top: 1997px; background: linear-gradient(180deg, #7a0d1e 0%, #8b1a2c 100%); color: var(--white); }
  .quote-slide .frame { position: absolute; inset: 19px; border: 1.5px dashed rgba(255,255,255,.6); }
  .rule-line { position: absolute; height: 2px; background: var(--white); }
  .rule-line::before, .rule-line::after { content: ""; position: absolute; top: -3px; width: 8px; height: 8px; border-radius: 50%; background: var(--white); }
  .rule-line::before { left: -4px; }
  .rule-line::after { right: -4px; }
  .quote-mark { position: absolute; left: 505px; top: 176px; width: 56px; height: 56px; border-radius: 50%; background: var(--white); }
  .quote-text { position: absolute; left: 100px; right: 100px; top: 248px; text-align: center; font-size: 18px; font-style: italic; font-weight: 500; line-height: 34px; }
  .quote-author { position: absolute; left: 0; right: 0; top: 361px; text-align: center; font-size: 17px; font-weight: 500; }

  /* Closing */
  .closing { top: 3288px; }
  .closing .hero { position: absolute; left: 0; top: 0; width: 100%; height: 404px; background: linear-gradient(180deg, #7d1020 0%, #8c1a2d 100%); text-align: center; color: var(--white); border-bottom: 4px solid #bdbdbd; }
  .closing .brand { top: 125px; font-size: 62px; line-height: 1; }
  .thanks { position: absolute; left: 0; right: 0; top: 250px; font-size: 44px; font-weight: 600; }
  .contact { position: absolute; top: 372px; width: 300px; margin-left: -150px; text-align: center; font-size: 15px; line-height: 22px; color: var(--body); }
  .contact .icon { width: 58px; height: 58px; margin: 0 auto 16px; background: #f4f4f4; box-shadow: 0 2px 4px rgba(0,0,0,.15); display: flex; align-items: center; justify-content: center; }
</style>
</head>
<body>

<section class="slide cover">
  <div class="scene" role="img" aria-label="Faded aerial view of an old town along a river, tinted red"></div>
  <div class="brand">HALDER</div>
  <h1 class="cover-title">Presentation Title</h1>
  <div class="cover-sub">Subtitle Of The Presentation</div>
  <div class="cover-url">WWW.HALDERFLEISCHHAUEREI.COM</div>
</section>

<section class="slide text-slide" style="top:704px">
  <div class="side"></div>
  <div class="photo" role="img" aria-label="Branded delivery van parked in front of an old brick farmhouse" style="background:linear-gradient(180deg,#8fa9c4 0%,#6d5a4c 35%,#3e4446 65%,#5c7a3a 100%)"></div>
  <div class="text-block">
    <h2>The standard Lorem Ipsum passage, used since the 1500s</h2>
    <p>Sed ut perspiciatis unde omnis iste natus eptatem accusantium doloremque laudantium, totam rem aperiam, eaque ipsa quae ab illo inventore veritatis et quasi architecto beatae vitae dicta sunt explicabo. Nemo enim ipsam voluptatem quia voluptas sit aspernatur aut odit aut fugit, sed qunsequuntur magni dolores eos qui ratione voluptatem sequesciunt. Neque porro quisquam est, qui dolorem ipsum quia dolor sit amet, consectetur, adipisci velit, sed quia non numquam eius di tempora incidunt ut labore et dolore magnam aliquam quaerat voluptatem.</p>
  </div>
  <div class="page-no"><span>01</span></div>
</section>

<section class="slide points-slide">
  <div class="side"></div>
  <div class="photo" role="img" aria-label="Hands holding a raw rib steak on a wooden board" style="left:20px;top:51px;width:203px;height:331px;background:linear-gradient(160deg,#3a2620,#8a3a35 50%,#4a2e24)"></div>
  <div class="photo" role="img" aria-label="Butcher working with hanging meat" style="left:20px;top:399px;width:203px;height:150px;background:linear-gradient(120deg,#b77a80,#7a4a4c 60%,#d8cfcf)"></div>
  <div class="photo" role="img" aria-label="Smiling butcher holding a steak and a cleaver" style="left:240px;top:51px;width:333px;height:498px;background:linear-gradient(180deg,#8ebfc6 0%,#7fb4bc 45%,#2a2a2a 100%)"></div>
  <ul class="points">
    <li><div class="num">01</div><div><h3>The standard Lorem</h3><p>Sed ut perspiciatcusantiuremque laudantium, totam rem aperiam, eaque ie ab illo</p></div></li>
    <li><div class="num">02</div><div><h3>The standard Lorem</h3><p>Sed ut perspiciatcusantiuremque laudantium, totam rem aperiam, eaque ie ab illo</p></div></li>
    <li><div class="num">03</div><div><h3>The standard Lorem</h3><p>Sed ut perspiciatcusantiuremque laudantium, totam rem aperiam, eaque ie ab illo</p></div></li>
  </ul>
  <div class="page-no"><span>02</span></div>
</section>

<section class="slide quote-slide">
  <div class="frame"></div>
  <div class="rule-line" style="left:139px;top:203px;width:784px"></div>
  <div class="quote-mark">
    <svg width="56" height="56" viewBox="0 0 56 56" aria-hidden="true">
      <path d="M19 21c-4 1-6 5-6 9v6h9v-8h-4c0-3 2-4 4-5zM33 21c-4 1-6 5-6 9v6h9v-8h-4c0-3 2-4 4-5z" fill="#7b0e1f"/>
    </svg>
  </div>
  <p class="quote-text">Lorem ipsum dolor sit amet, consectetur adipiscing elit, sed do eiusmod tempor incididunt ut labore et dolore magna aliqua. Quis ipsum suspendisse ultrices gravida. Risus commodo viverra maecenas accumsan lacus vel facilisis.</p>
  <div class="quote-author">- Jane Miller</div>
  <div class="rule-line" style="left:252px;top:411px;width:559px"></div>
</section>

<section class="slide text-slide" style="top:2642px">
  <div class="side"></div>
  <div class="photo" role="img" aria-label="Branded delivery van parked on grass beside a stone barn" style="background:linear-gradient(180deg,#6b5a4c 0%,#4a4b4a 40%,#3f4f66 62%,#5f8a3a 100%)"></div>
  <div class="text-block">
    <h2>The standard Lorem Ipsum passage, used since the 1500s</h2>
    <p>Sed ut perspiciatis unde omnis iste natus eptatem accusantium doloremque laudantium, totam rem aperiam, eaque ipsa quae ab illo inventore veritatis et quasi architecto beatae vitae dicta sunt explicabo. Nemo enim ipsam voluptatem quia voluptas sit aspernatur aut odit aut fugit, sed qunsequuntur magni dolores eos qui ratione voluptatem sequesciunt. Neque porro quisquam est, qui dolorem ipsum quia dolor sit amet, consectetur, adipisci velit, sed quia non numquam eius di tempora incidunt ut labore et dolore magnam aliquam quaerat voluptatem.</p>
  </div>
  <div class="page-no"><span>05</span></div>
</section>

<section class="slide closing">
  <div class="hero" role="img" aria-label="Faded meat cuts on a board, tinted red">
    <div class="brand">HALDER</div>
    <div class="thanks">THANK YOU</div>
  </div>
  <div class="contact" style="left:200px">
    <div class="icon"><svg width="22" height="26" viewBox="0 0 22 26" aria-hidden="true"><path d="M11 1a9 9 0 0 0-9 9c0 7 9 15 9 15s9-8 9-15a9 9 0 0 0-9-9zm0 12.5a3.5 3.5 0 1 1 0-7 3.5 3.5 0 0 1 0 7z" fill="#7b0e1f"/></svg></div>
    1234 Somestreet Anywhere<br>USA 21212
  </div>
  <div class="contact" style="left:522px">
    <div class="icon"><svg width="26" height="26" viewBox="0 0 24 24" aria-hidden="true"><path d="M6.6 10.8a15.5 15.5 0 0 0 6.6 6.6l2.2-2.2c.3-.3.7-.4 1-.2 1.1.4 2.3.6 3.6.6.6 0 1 .4 1 1V20c0 .6-.4 1-1 1A17 17 0 0 1 3 4c0-.6.4-1 1-1h3.5c.6 0 1 .4 1 1 0 1.2.2 2.4.6 3.6.1.3 0 .7-.2 1z" fill="#7b0e1f"/></svg></div>
    Phone:<br>(888) 888 - 8888
  </div>
  <div class="contact" style="left:838px">
    <div class="icon"><svg width="28" height="20" viewBox="0 0 28 20" aria-hidden="true"><rect x="1" y="1" width="26" height="18" fill="#7b0e1f"/><path d="M1 1l13 10L27 1" stroke="#f4f4f4" stroke-width="1.6" fill="none"/></svg></div>
    Email:<br>info@halderfleischhauerei.com
  </div>
</section>

</body>
</html>
```